Sleek wordpress site for Bramblecrest finishing works

We are a commercial job shop that serves B2B, govt & LEO and retail clients.We need a wordpress site with 6 individual pages: homepage, coating, laser engraving, laser cutting, part marking, and contact us. I have attached an outline of the desired flow and sub headings for each page. I would like to incorporate the colors of the logo through out the site to be clean and sleek enough to appeal to B2B commercial clients yet be inviting enough for retail clients.

I would like to have easy picture functionality so photographs on each page can be updated easily.

Target Market(s)

B2B industrial & Govt and Military part marking, laser engraving and coating: machine shops, aerospace companies, tool manufactures. Retail: personalized gifts, Job Shop

Coding

Coded - Design and coding required

Font styles to use
Sans Serif
Other font styles liked:
• Open to suggestion

Colors
0255a3
3176b5
eaf1f7
cfdeed
ffffff

Requirements
Must have
• Clean easy to navigate flow, separate pages as indicated on attached outline, high class feel. Great picture functionality, professional and inviting feel,
• **update: needs to be optimized for mobile, should have a gallery function. Gallery can be an additional page or embedded
Nice to have
• Social media connectivity links,
Should not have
• crappy plugins that make back-end management difficult, no blog

```html
<!DOCTYPE html>
<html lang="en">
<head>
<meta charset="utf-8">
<title>Bramblecrest Finishing Works</title>
<link rel="stylesheet" href="https://fonts.googleapis.com/css2?family=Roboto:wght@400;500;700&family=Lato:wght@400;700&display=swap">
<style>
:root{
  --brand:#0255a3;
  --brand-mid:#3176b5;
  --ice:#eaf1f7;
  --mist:#cfdeed;
  --white:#ffffff;
  --ink:#111111;
  --body:#666666;
  --panel:#f2f2f2;
  --frame:#d9dadc;
  --field:#e3e3e3;
  --dark:#1b1c1f;
}
*{margin:0;padding:0;box-sizing:border-box}
html,body{width:1200px;height:2731px;overflow:hidden;background:var(--white)}
body{position:relative;font-family:'Lato',sans-serif;color:var(--body)}
.abs{position:absolute}

/* hero */
.hero-frame{left:0;top:0;width:1200px;height:662px;background:linear-gradient(180deg,#c9cacd,#e8e8e9);clip-path:polygon(0 0,100% 0,100% 545px,50% 662px,0 545px)}
.hero-photo{left:16px;top:16px;width:1168px;height:636px;clip-path:polygon(0 0,100% 0,100% 524px,50% 636px,0 524px);
  background:radial-gradient(circle at 900px 360px,rgba(255,196,110,.85) 0,rgba(214,140,60,.35) 60px,transparent 190px),
  radial-gradient(circle at 920px 180px,#8a8d92 0,#4a4c50 220px,transparent 420px),
  linear-gradient(160deg,#3a3b3e 0%,#222326 45%,#55575b 75%,#2a2b2e 100%)}
.nav{top:62px;left:0;width:1200px;height:24px}
.brand{left:78px;top:46px;display:flex;align-items:center;gap:10px;color:var(--white);font-family:'Lato',sans-serif;font-weight:700;font-size:17px;line-height:20px;width:200px}
.brand-dot{width:34px;height:34px;border:2px solid var(--white);border-radius:50%;flex:none}
.nav a{position:absolute;top:0;color:var(--white);text-decoration:none;font-size:16px;font-weight:700;font-family:'Lato',sans-serif}
.cart{left:1100px;top:60px}
.hero-title{left:78px;top:208px;color:var(--white);font-family:'Roboto',sans-serif;font-weight:700;font-size:26px;line-height:36px;text-transform:uppercase}
.hero-text{left:78px;top:303px;width:400px;color:var(--white);font-size:15px;line-height:26px}
.btn{position:absolute;display:flex;align-items:center;justify-content:center;font-family:'Roboto',sans-serif;font-weight:700;font-size:17px;color:var(--white);border-radius:3px}
.btn-ghost{left:78px;top:391px;width:145px;height:52px;border:2px solid var(--white);background:#161719}
.btn-solid{left:233px;top:391px;width:146px;height:52px;background:var(--brand)}
.scroll-cue{width:36px;height:36px}

/* about */
.section-title{left:0;width:1200px;text-align:center;color:var(--brand);font-family:'Roboto',sans-serif;font-weight:700;font-size:29px}
.about-copy{left:275px;top:778px;width:650px;text-align:center;font-size:15px;line-height:26px}
.about-copy p+p{margin-top:26px}
.btn-more{left:528px;top:970px;width:144px;height:52px;background:var(--brand)}

/* newsletter */
.news-frame{left:0;top:1085px;width:1200px;height:300px;background:linear-gradient(180deg,#cfd0d3,#ececed);clip-path:polygon(0 100px,50% 0,100% 100px,100% 100%,0 100%)}
.news-photo{left:16px;top:1100px;width:1168px;height:270px;clip-path:polygon(0 102px,50% 0,100% 102px,100% 100%,0 100%);
  background:radial-gradient(circle at 380px 200px,rgba(246,170,80,.75) 0,rgba(190,110,40,.3) 70px,transparent 230px),
  linear-gradient(90deg,#3e3f42 0%,#1c1d20 40%,#111214 100%)}
.news-title{left:0;top:1152px;width:1200px;text-align:center;color:var(--white);font-family:'Roboto',sans-serif;font-weight:700;font-size:29px}
.news-sub{left:0;top:1219px;width:1200px;text-align:center;color:var(--white);font-size:15px}
.news-field{left:429px;top:1275px;width:342px;height:47px;border:2px solid var(--white);border-radius:24px;color:var(--white);font-size:15px;padding:13px 18px}
.news-send{left:724px;top:1279px;width:39px;height:39px;border-radius:50%;background:var(--white)}

/* services */
.services-band{left:0;top:1384px;width:1200px;height:493px;background:var(--panel);clip-path:polygon(0 0,100% 0,100% 379px,50% 493px,0 379px)}
.service{top:1510px;width:250px;text-align:center}
.service-icon{width:86px;height:86px;margin:0 auto;border-radius:50%;background:var(--brand);box-shadow:0 0 0 4px var(--mist)}
.service h3{margin-top:25px;color:var(--ink);font-family:'Roboto',sans-serif;font-weight:700;font-size:19px}
.service p{margin-top:6px;font-size:14px;line-height:26px}
.service a{color:var(--brand);font-weight:700;text-decoration:underline}

/* contact */
.field{position:absolute;border:2px solid var(--field);background:var(--white);font-size:14px;color:var(--body);padding:16px 14px;border-radius:3px}
.btn-submit{left:528px;top:2180px;width:144px;height:51px;background:var(--brand)}

/* footer */
.foot-frame{left:0;top:2291px;width:1200px;height:440px;background:linear-gradient(180deg,#c7c8cb,#e9e9ea);clip-path:polygon(0 104px,50% 0,100% 104px,100% 100%,0 100%)}
.foot-photo{left:16px;top:2309px;width:1168px;height:404px;clip-path:polygon(0 110px,50% 0,100% 110px,100% 100%,0 100%);
  background:radial-gradient(circle at 820px 120px,rgba(205,150,80,.6) 0,transparent 300px),
  linear-gradient(180deg,rgba(40,38,36,.92),#141518)}
.foot-head{color:var(--white);font-family:'Roboto',sans-serif;font-weight:700;font-size:18px}
.foot-link{position:absolute;color:var(--white);font-size:15px;display:flex;align-items:center;gap:16px}
.foot-text{position:absolute;color:var(--white);font-size:15px;line-height:26px}
.foot-brand{left:862px;top:2458px;width:200px;text-align:center;color:var(--white);font-weight:700;font-size:17px;line-height:22px}
.social{top:2562px;width:36px;height:36px;border-radius:50%;background:#6f7073}
.rule{left:78px;top:2646px;width:1044px;height:1px;background:rgba(255,255,255,.35)}
.copyright{left:0;top:2670px;width:1200px;text-align:center;color:var(--white);font-size:15px}
.copyright b{font-weight:700}
</style>
</head>
<body>

<header>
  <div class="abs hero-frame"></div>
  <div class="abs hero-photo" role="img" aria-label="Photo of a laser cutting head throwing sparks over a metal sheet"></div>
  <div class="abs brand"><span class="brand-dot"></span>Bramblecrest Finishing Works</div>
  <nav class="abs nav">
    <a style="left:397px">Home</a>
    <a style="left:475px">Coating</a>
    <a style="left:566px">Laser Engraving</a>
    <a style="left:712px">Laser Cutting</a>
    <a style="left:841px">Part Marketing</a>
    <a style="left:980px">Contact Us</a>
  </nav>
  <svg class="abs cart" width="24" height="22" viewBox="0 0 24 22" fill="none" stroke="#fff" stroke-width="2"><path d="M2 8h20l-3 12H5z"/><path d="M7 8l5-6 5 6"/></svg>
  <h1 class="abs hero-title">Bramblecrest<br>Finishing Works</h1>
  <p class="abs hero-text">Lorem Ipsum is simply dummy text of the printing and typesetting industry.</p>
  <div class="btn btn-ghost">Contact Us</div>
  <div class="btn btn-solid">Get A Quote</div>
  <svg class="abs scroll-cue" style="left:582px;top:574px" viewBox="0 0 36 36" fill="none" stroke="#333" stroke-width="2"><circle cx="18" cy="18" r="16"/><path d="M18 10v15M12 19l6 6 6-6"/></svg>
</header>

<section class="about">
  <h2 class="abs section-title" style="top:716px">About Bramblecrest Finishing Works</h2>
  <div class="abs about-copy">
    <p>Lorem Ipsum is simply dummy text of the printing and typesetting industry. Lorem Ipsum has been the industry's standard dummy text ever since the 1500s, when an unknown printer took a galley of type and scrambled it to make a type specimen book.</p>
    <p>It has survived not only five centuries, but also the leap into electronic typesetting, remaining essentially unchanged.</p>
  </div>
  <div class="btn btn-more">Know More</div>
</section>

<section class="newsletter">
  <div class="abs news-frame"></div>
  <div class="abs news-photo" role="img" aria-label="Photo of a laser nozzle cutting metal with a spray of sparks"></div>
  <h2 class="abs news-title">Newsletter</h2>
  <p class="abs news-sub">For Latest news or updates subscribe our newsletter</p>
  <div class="abs news-field">Enter e-mail here...</div>
  <svg class="abs news-send" viewBox="0 0 39 39"><path d="M11 19l17-8-6 17-3-6z" fill="#111"/></svg>
</section>

<section class="services">
  <div class="abs services-band"></div>
  <h2 class="abs section-title" style="top:1446px">Our Services</h2>

  <div class="abs service" style="left:70px">
    <svg class="service-icon" viewBox="0 0 86 86" fill="none" stroke="#fff" stroke-width="3"><path d="M36 32h18v10H36zM48 42v14h-6V42M30 34h-6M30 38h-8M30 42h-6"/></svg>
    <h3>Coating</h3>
    <p>Vellacoat is a spray on ceramic based finish that can be applied to metals,....<a>Read More</a></p>
  </div>
  <div class="abs service" style="left:339px">
    <svg class="service-icon" viewBox="0 0 86 86" fill="none" stroke="#fff" stroke-width="3"><path d="M31 28h24M35 33h16l-4 10h-8zM43 43v9M30 58h26"/></svg>
    <h3>Laser engraving</h3>
    <p>Capabilities Statement: With our selection of CO2 and fiber lasers there are very.....<a>Read More</a></p>
  </div>
  <div class="abs service" style="left:609px">
    <svg class="service-icon" viewBox="0 0 86 86" fill="none" stroke="#fff" stroke-width="3"><path d="M38 26h10v12l-5 8-5-8zM43 48v8M34 52l4 3M52 52l-4 3M30 60h26"/></svg>
    <h3>Laser Cutting</h3>
    <p>What is laser cutting: Laser cutting is a non-contact cutting process with....<a>Read More</a></p>
  </div>
  <div class="abs service" style="left:880px">
    <svg class="service-icon" viewBox="0 0 86 86" fill="none" stroke="#fff" stroke-width="3"><path d="M31 57l3-10 18-18 7 7-18 18zM48 33l7 7"/></svg>
    <h3>Part Marking</h3>
    <p>o&nbsp; Picture slider<br>o&nbsp; Capabilities<br>Barcodes ....<a>Read More</a></p>
  </div>
  <svg class="abs scroll-cue" style="left:582px;top:1855px" viewBox="0 0 36 36" fill="none" stroke="#0255a3" stroke-width="2"><circle cx="18" cy="18" r="16" fill="#fff"/><path d="M18 10v15M12 19l6 6 6-6"/></svg>
</section>

<section class="contact">
  <h2 class="abs section-title" style="top:1956px">Contact Us</h2>
  <div class="field" style="left:151px;top:2021px;width:295px;height:53px">Name*</div>
  <div class="field" style="left:453px;top:2021px;width:295px;height:53px">E-mail*</div>
  <div class="field" style="left:756px;top:2021px;width:293px;height:53px">Phone*</div>
  <div class="field" style="left:151px;top:2085px;width:898px;height:84px">Message</div>
  <div class="btn btn-submit">Submit</div>
</section>

<footer>
  <div class="abs foot-frame"></div>
  <div class="abs foot-photo" role="img" aria-label="Dark photo of laser cutting equipment with warm sparks"></div>

  <div class="abs foot-head" style="left:78px;top:2438px">Navigation</div>
  <div class="foot-link" style="left:78px;top:2480px"><span>›</span>Home</div>
  <div class="foot-link" style="left:78px;top:2511px"><span>›</span>Coating</div>
  <div class="foot-link" style="left:78px;top:2542px"><span>›</span>Laser Engraving</div>
  <div class="foot-link" style="left:78px;top:2573px"><span>›</span>Laser Cutting</div>
  <div class="foot-link" style="left:255px;top:2480px"><span>›</span>Part Marketing</div>
  <div class="foot-link" style="left:255px;top:2511px"><span>›</span>Contact Us</div>

  <div class="abs foot-head" style="left:441px;top:2438px">Get In Touch</div>
  <svg class="abs" style="left:440px;top:2480px" width="16" height="20" viewBox="0 0 16 20"><path d="M8 0a7 7 0 0 0-7 7c0 5 7 13 7 13s7-8 7-13a7 7 0 0 0-7-7z" fill="#fff"/><circle cx="8" cy="7" r="2.5" fill="#222"/></svg>
  <p class="foot-text" style="left:477px;top:2476px">418 N Alder Row #7,<br>Tempe, AZ 85281</p>
  <svg class="abs" style="left:439px;top:2550px" width="18" height="18" viewBox="0 0 18 18"><path d="M4 1l3 4-2 2c1 3 3 5 6 6l2-2 4 3-2 3C7 17 1 11 1 3z" fill="#fff"/></svg>
  <p class="foot-text" style="left:477px;top:2546px">480.555.0142</p>
  <svg class="abs" style="left:438px;top:2604px" width="20" height="14" viewBox="0 0 20 14" fill="none" stroke="#fff" stroke-width="2"><rect x="1" y="1" width="18" height="12"/><path d="M1 1l9 7 9-7"/></svg>
  <p class="foot-text" style="left:477px;top:2598px">hello@bramblecrestworks.com</p>

  <div class="abs foot-brand">Bramblecrest<br>Finishing Works</div>
  <div class="abs social" style="left:880px" aria-label="Social link"></div>
  <div class="abs social" style="left:922px" aria-label="Social link"></div>
  <div class="abs social" style="left:965px" aria-label="Social link"></div>
  <div class="abs social" style="left:1007px" aria-label="Social link"></div>

  <div class="abs rule"></div>
  <p class="abs copyright"><b>© BFW BRAMBLECREST FINISHING WORKS - 2018.</b> All Rights Reserved.</p>
</footer>

</body>
</html>
```